Personal Training Business at home (Fern Vitality & Health)

My business name will be Fern Vitality & Health and will be training people with special needs (Asthma, Diabetes, Obesity, Rehab, Sports Performance) for all ages. It will be set indoor and outdoor for all types of weather conditions. I,m also doing Pilates group classes as well in a Japanese garden setting.I will be working alone so the groups will be small and the client has a high quality of service. I just need something very basic to start with then as the business expands I can edit it to it,s growth.

Target Market(s)

Target special population persons with dysfunctions injuries, metabolic/cardio-respiratory conditions, sports performance and more also healthy food choices.

Industry/Entity Type

Business

Number of Pages Required

3 page

Font styles to use
Serif

Colors
f78f20
ffffff
474747
cbcbcb
abd036

Requirements
Must have
• The website must have accessibility for change, to be able to link on other networks like my own YouTube videos. A basic lay out so I can fill in the pages and ad more as I expand the business. The logo to have the A for Fern to be an image of a man shaped as the letter A with his arms extended out/up. Private Facility and must ring for appointment to enter premises.
Nice to have
• The Image I want to have in my studio is for people to be serious about training & health choices. I want them to be able to train in a comfortable environment and free of air conditioned concrete rooms with machines. My home is converted to a Organic feature and outdoor/indoor training facility that my clients & I can share the natural freedom of training in the elements. My client have special needs and need extra care, they are people with injuries, metabolic/cardio-respiratory condition, asthmatics & more they need to be screened and tested for the condition that they suffer from and together with there allied professional we work together to treat them with the up most care for maximum results. This is what I want to target I long term client with real Goals on there mind and not some pipe dream.
Should not have
• Not to be portray as a Gym with machines and clients that only care about image.

```html
<!DOCTYPE html>
<html lang="en">
<head>
<meta charset="utf-8">
<title>Fern Fitness — Personal Training from Home</title>
<link href="https://fonts.googleapis.com/css2?family=Open+Sans:wght@400;600&family=Ruda:wght@400;700&display=swap" rel="stylesheet">
<style>
:root{
  --orange:#f78f20;
  --green:#abd036;
  --white:#ffffff;
  --ink:#474747;
  --mist:#cbcbcb;
  --footer:#1b1b1b;
  --footer-base:#121212;
  --body:#555555;
}
*{margin:0;padding:0;box-sizing:border-box}
html,body{width:1200px;height:3005px;overflow:hidden;background:var(--white)}
body{font-family:"Open Sans",sans-serif;color:var(--ink);position:relative}
.heading{font-family:"Ruda",sans-serif;font-weight:400;letter-spacing:.5px}

/* header */
.accent-bar{position:absolute;top:0;left:0;width:1200px;height:5px;background:var(--orange);z-index:3}
.site-header{position:absolute;top:5px;left:0;width:1200px;height:113px;background:rgba(20,20,20,.72);z-index:2}
.contact-strip{position:absolute;top:14px;right:144px;display:flex;gap:34px;font-size:11px;color:var(--white)}
.contact-strip span{display:flex;align-items:center;gap:8px}
.logo{position:absolute;left:144px;top:42px;font-family:"Ruda",sans-serif;font-size:28px;color:var(--white);letter-spacing:.5px}
.main-nav{position:absolute;top:56px;right:144px;display:flex;gap:30px;font-size:10.5px;color:var(--white);text-transform:uppercase;font-weight:600}

/* hero */
.hero{position:absolute;top:0;left:0;width:1200px;height:638px;background:linear-gradient(160deg,#5b4738 0%,#8a6447 35%,#a57a57 60%,#7a5a42 100%)}
.hero-plant{position:absolute;left:0;top:110px;width:300px;height:528px;background:radial-gradient(ellipse at 45% 40%,#5f7d3a 0%,#3f5a2a 45%,rgba(140,80,60,.0) 75%)}
.hero-title{position:absolute;top:330px;width:1200px;text-align:center;font-size:29px;color:var(--white)}
.btn{position:absolute;display:flex;align-items:center;justify-content:center;color:var(--white);font-family:"Ruda",sans-serif;font-size:17px;letter-spacing:.5px}
.btn-green{background:var(--green);left:490px;top:400px;width:218px;height:56px}
.slider-dots{position:absolute;top:584px;left:590px;display:flex;gap:6px}
.slider-dots i{width:8px;height:8px;border-radius:50%;background:rgba(255,255,255,.7)}
.slider-dots i.active{background:var(--orange)}

/* welcome */
.welcome{position:absolute;top:638px;left:0;width:1200px;height:362px;background:var(--white)}
.portrait{position:absolute;left:192px;top:56px;width:236px;height:236px;border-radius:50%;border:8px solid var(--orange);background:radial-gradient(circle at 50% 40%,#8aa86a,#4d6f3a 70%,#2f4a6a);box-shadow:0 4px 10px rgba(0,0,0,.25)}
.welcome-title{position:absolute;left:460px;top:80px;font-size:28px;color:var(--green)}
.welcome-text{position:absolute;left:460px;top:142px;width:600px;font-size:13.5px;line-height:23px;color:var(--ink)}

/* why */
.why{position:absolute;top:1000px;left:0;width:1200px;height:522px;background:linear-gradient(180deg,#5e5e5e 0%,#8b8b8b 45%,#b3b3b3 70%,#6f6f6f 100%)}
.why-title{position:absolute;top:162px;width:1200px;text-align:center;font-size:30px;color:var(--white)}
.why-text{position:absolute;top:226px;left:150px;width:900px;text-align:center;font-size:13.5px;line-height:22px;color:var(--white)}
.btn-orange{background:var(--orange);left:490px;top:372px;width:220px;height:58px}

/* services */
.services{position:absolute;top:1522px;left:0;width:1200px;height:514px;background:var(--white)}
.services-title{position:absolute;top:70px;width:1200px;text-align:center;font-size:28px;color:var(--green)}
.service-card{position:absolute;top:148px;width:286px}
.service-card .photo{height:148px}
.service-card h3{font-family:"Open Sans",sans-serif;font-weight:400;font-size:13px;text-transform:uppercase;color:var(--ink);margin-top:22px;padding-bottom:10px;border-bottom:2px solid var(--orange);letter-spacing:.3px}
.service-card p{font-size:10.5px;line-height:18px;color:#7a7a7a;margin-top:14px}
.arrow{position:absolute;top:274px}

/* video */
.featured{position:absolute;top:2036px;left:0;width:1200px;height:584px;background:radial-gradient(ellipse at 70% 40%,#e6e6e6 0%,#bdbdbd 40%,#8a8a8a 100%)}
.featured-title{position:absolute;top:56px;width:1200px;text-align:center;font-size:26px;color:var(--ink)}
.video-frame{position:absolute;left:224px;top:126px;width:752px;height:374px;background:linear-gradient(120deg,#e9f08a 0%,#8cc03c 35%,#3f7a26 70%,#2b5a1d 100%);box-shadow:0 6px 18px rgba(0,0,0,.35)}
.play{position:absolute;left:344px;top:155px}

/* footer */
.site-footer{position:absolute;top:2620px;left:0;width:1200px;height:315px;background:var(--footer);color:#d0d0d0}
.footer-col{position:absolute;top:56px}
.footer-col h4{font-family:"Ruda",sans-serif;font-weight:400;font-size:13px;color:var(--orange);text-transform:uppercase;letter-spacing:.4px;margin-bottom:28px}
.footer-col p{font-size:9.5px;line-height:15px;width:200px}
.footer-list{list-style:none;font-size:9.5px}
.footer-list li{margin-bottom:11px;padding-left:18px;position:relative}
.footer-list li::before{content:"›";position:absolute;left:2px;top:-2px;font-size:12px}
.hours-label{color:var(--green);font-size:10.5px;margin:-4px 0 10px}
.hours-list{list-style:none;font-size:9.5px;margin-bottom:20px}
.hours-list li{margin-bottom:5px;padding-left:18px;position:relative}
.hours-list li::before{content:"›";position:absolute;left:2px;top:-2px;font-size:12px}
.social{display:flex;gap:12px;margin-top:-4px}
.social i{width:12px;height:12px;border-radius:50%;background:#d0d0d0}
.footer-base{position:absolute;top:2935px;left:0;width:1200px;height:70px;background:var(--footer-base);color:#cfcfcf;font-size:10px}
.footer-base .copy{position:absolute;left:144px;top:30px}
.footer-base .legal{position:absolute;right:144px;top:30px}
.footer-base .legal span{margin:0 8px}
</style>
</head>
<body>

<div class="hero" role="img" aria-label="Photo of a sunlit timber deck in a home garden studio with a potted plant">
  <div class="hero-plant"></div>
</div>

<div class="accent-bar"></div>
<header class="site-header">
  <div class="contact-strip">
    <span><svg width="11" height="8" viewBox="0 0 11 8"><rect x=".5" y=".5" width="10" height="7" fill="none" stroke="#abd036"/><path d="M.5 .5 5.5 4.5 10.5 .5" fill="none" stroke="#abd036"/></svg>Email: fernfithealth@mailbox.example</span>
    <span><svg width="10" height="10" viewBox="0 0 10 10"><path d="M2 0 4 2.5 3 4C4 6 5 7 6.5 7.5L8 6.5 10 8.5 8.5 10C4 9.5 .5 6 0 1.5Z" fill="#abd036"/></svg>Mobile: 0400 123 987</span>
  </div>
  <div class="logo"><span style="color:var(--orange)">FERN</span> FITNESS</div>
  <nav class="main-nav">
    <span>Home</span><span>About Us</span><span>Why Train With Us</span><span>Training Services</span><span>Location</span><span>Pricing &amp; Packages</span><span>Contact Us</span>
  </nav>
</header>

<h1 class="hero-title heading">We are a personal training &amp; fitness company from home</h1>
<div class="btn btn-green">LEARN MORE</div>
<div class="slider-dots"><i class="active"></i><i></i><i></i><i></i></div>

<section class="welcome">
  <div class="portrait" role="img" aria-label="Portrait photo of the personal trainer in his garden"></div>
  <h2 class="welcome-title heading">WELCOME TO FERN FITNESS</h2>
  <p class="welcome-text">All my life I have been looking for a place that I can train in a comfortable and natural environment instead been surrounded by concrete walls &amp; floors, what I am offering in my studio gym is a natural organic style of training that clients can feel whatit's like to be outside in the elements. This is something that you can come feel &amp; enjoy the pleasure of training in the outdoors and still accomplishing your goals.</p>
</section>

<section class="why" role="img" aria-label="Black and white photo of the timber deck training area">
  <h2 class="why-title heading">WHY TRAIN WITH US</h2>
  <p class="why-text">Our training services covers a wide variety of clients from different walks of life, like builders, plumbers, electricians, mechanics, truck drivers to your everyday common office workers, teachers, taxi drivers, nurses &amp; doctors and more. All these people are all eligible for this type of training. It is a great way to restore functional movement to deal with the everyday demands of your body &amp; just general fitness, health &amp; wellbeing.</p>
  <div class="btn btn-orange">LEARN MORE</div>
</section>

<section class="services">
  <h2 class="services-title heading">TRAINING SERVICES</h2>
  <svg class="arrow" style="left:66px" width="12" height="16" viewBox="0 0 12 16"><path d="M9 2 3 8 9 14" fill="none" stroke="#474747" stroke-width="2"/></svg>
  <svg class="arrow" style="left:1120px" width="12" height="16" viewBox="0 0 12 16"><path d="M3 2 9 8 3 14" fill="none" stroke="#474747" stroke-width="2"/></svg>

  <article class="service-card" style="left:144px">
    <div class="photo" role="img" aria-label="Photo of a trainer assisting a client on the grass" style="background:linear-gradient(180deg,#9cc46a,#4d8a34 60%,#3a6e2a)"></div>
    <h3>Personal Training One on One</h3>
    <p>At vero eos et accusamus et iusto odio dignissimos ducimus qui blanditiis praesentium voluptatum deleniti atque corrupti quos dolores et quas molestias excepturi sint occaecati cupiditate</p>
  </article>
  <article class="service-card" style="left:456px">
    <div class="photo" role="img" aria-label="Photo of a group stretching outdoors in a park" style="background:linear-gradient(180deg,#b6d68a,#6ea046 55%,#4a7a30)"></div>
    <h3>Group Functional Training</h3>
    <p>At vero eos et accusamus et iusto odio dignissimos ducimus qui blanditiis praesentium voluptatum deleniti atque corrupti quos dolores et quas molestias excepturi sint occaecati cupiditate</p>
  </article>
  <article class="service-card" style="left:766px">
    <div class="photo" role="img" aria-label="Photo of a runner on a tree lined path" style="background:linear-gradient(180deg,#cfe08a,#7aa640 50%,#9a8a5a)"></div>
    <h3>Sports Performance</h3>
    <p>At vero eos et accusamus et iusto odio dignissimos ducimus qui blanditiis praesentium voluptatum deleniti atque corrupti quos dolores et quas molestias excepturi sint occaecati cupiditate</p>
  </article>
</section>

<section class="featured" role="img" aria-label="Faded black and white photo of a woman exercising">
  <h2 class="featured-title heading">FEATURED VIDEO</h2>
  <div class="video-frame" role="img" aria-label="Video still of a woman jogging outdoors in sunlight">
    <svg class="play" width="64" height="64" viewBox="0 0 64 64"><circle cx="32" cy="32" r="30" fill="#ffffff" stroke="#c8161d" stroke-width="5"/><circle cx="32" cy="32" r="22" fill="#c8161d"/><path d="M26 21 44 32 26 43Z" fill="#ffffff"/></svg>
  </div>
</section>

<footer class="site-footer">
  <div class="footer-col" style="left:144px">
    <h4>About Fern Fit &amp; Health</h4>
    <p>FERNFIT has trainers that have a Diploma of fitness from the Birchwood Institute are trained and qualified with the latest training techniques available anywhere in Australia, to give clients a better &amp; more reliable service with cutting edge training programs and testing.</p>
  </div>
  <div class="footer-col" style="left:376px">
    <h4>Training Services</h4>
    <ul class="footer-list">
      <li>Personal training one on one</li>
      <li>Group functional training</li>
      <li>Sports performance</li>
      <li>Pilates</li>
      <li>Recovery &amp; stretching classes</li>
      <li>Rehabilitation programs</li>
      <li>Basic lifestyle choice plans</li>
    </ul>
  </div>
  <div class="footer-col" style="left:610px">
    <h4>Trading Hours</h4>
    <p class="hours-label">April - September</p>
    <ul class="hours-list">
      <li>Monday – Friday 4.00pm - 6.00pm (Finish by 7:00pm)</li>
      <li>Saturday- 12:00pm – 5:00pm (Finish by 6:00pm)</li>
      <li>Sunday - 6.00am – 11:00am (Finish by 12:00pm)</li>
    </ul>
    <p class="hours-label">October – March</p>
    <ul class="hours-list">
      <li>Monday – Friday 6.00pm – 7:00pm (Finish by 8:00pm)</li>
      <li>Saturday – 12:00pm – 5:00pm (Finish by 6:00pm)</li>
      <li>Sunday- 6:00am – 11:00am (Finish by 12:00pm)</li>
    </ul>
  </div>
  <div class="footer-col" style="left:898px">
    <h4>Follow Us</h4>
    <div class="social"><i></i><i></i><i></i><i></i><i></i><i></i></div>
  </div>
</footer>
<div class="footer-base">
  <span class="copy">© 2016 Company Name &nbsp;| &nbsp;All Rights Reserved</span>
  <span class="legal">Terms Of Service<span>|</span>Privacy Policy</span>
</div>

</body>
</html>
```